TalkHarbor - Language Coaching Services

Sleek, innovative, trendy design for Language Coaching business.

TalkHarbor is a new UK based company that provides Language Coaching services. We offer highly personalized on-line and face to face language courses. We also impart learning techniques workshops based on the latest neuroscience research for second-language acquisition.

Target Market(s)

See attached info

Industry/Entity Type

Consulting

Contact Information for Business Card

TalkHarbor
DaniaKV@talkharbor.co.uk
TalkHarbor.co.uk
London, UK

Font styles to use
Sans Serif

```html
<!DOCTYPE html>
<html lang="en">
<head>
<meta charset="utf-8">
<title>TalkHarbor Business Card</title>
<link href="https://fonts.googleapis.com/css2?family=Montserrat:wght@500;700&family=Roboto:wght@400&display=swap" rel="stylesheet">
<style>
  :root {
    --page: #dcdcdc;
    --card-white: #ffffff;
    --card-dark: #1b1c1e;
    --brand-blue: #0a8fc6;
    --brand-blue-deep: #0078ad;
    --brand-blue-light: #1a9bd0;
    --name-blue: #1679ad;
    --text-grey: #6d6d6d;
    --title-grey: #8a8a8a;
    --light-text: #e6e6e6;
  }
  * { box-sizing: border-box; margin: 0; padding: 0; }
  html, body {
    width: 1125px; height: 1200px; overflow: hidden;
    background: var(--page);
  }
  .canvas { position: relative; width: 1125px; height: 1200px; }
  .card {
    position: absolute; left: 150px; width: 825px; height: 470px;
    border-radius: 22px; overflow: hidden;
  }
  .card--front { top: 98px; background: var(--card-white); }
  .card--back { top: 631px; background: var(--card-dark); }

  .front__panel { position: absolute; left: 0; top: 0; width: 400px; height: 470px; }

  .front__mark {
    position: absolute; left: 576px; top: 45px; width: 116px; height: 116px;
    border: 7px solid var(--brand-blue); border-radius: 50%;
  }
  .wordmark {
    font-family: "Montserrat", sans-serif; font-weight: 500; color: var(--brand-blue);
    white-space: nowrap;
  }
  .front__wordmark {
    position: absolute; right: 50px; top: 166px; font-size: 42px; letter-spacing: 0.5px;
  }
  .person { position: absolute; right: 78px; top: 270px; text-align: right;
    font-family: "Montserrat", sans-serif; font-weight: 700; }
  .person__name { font-size: 28px; color: var(--name-blue); letter-spacing: 1px; line-height: 36px; }
  .person__title { font-size: 20px; color: var(--title-grey); letter-spacing: 1px; line-height: 24px; }

  .contacts { position: absolute; right: 76px; top: 448px; list-style: none; }
  .contacts li {
    display: flex; justify-content: flex-end; align-items: center; gap: 9px;
    font-family: "Roboto", sans-serif; font-size: 19px; color: var(--text-grey);
    height: 27px; letter-spacing: 0.4px;
  }
  .contacts svg { width: 18px; height: 18px; flex: none; }
  .contacts { top: 333px; }

  .back__ring {
    position: absolute; left: 281px; top: 93px; width: 262px; height: 262px;
    border: 12px solid var(--brand-blue); border-radius: 50%;
    display: flex; align-items: center; justify-content: center;
  }
  .back__wordmark { font-size: 38px; }
  .back__site {
    position: absolute; left: 0; right: 0; top: 400px; text-align: center;
    font-family: "Roboto", sans-serif; font-size: 19px; color: var(--light-text);
    letter-spacing: 7px;
  }
</style>
</head>
<body>
<main class="canvas">
  <section class="card card--front">
    <svg class="front__panel" viewBox="0 0 400 470" role="img" aria-label="Large blue arrow decoration panel">
      <defs>
        <linearGradient id="panelFill" x1="0" y1="0" x2="1" y2="1">
          <stop offset="0" stop-color="#0077ab"/>
          <stop offset="1" stop-color="#0a90c8"/>
        </linearGradient>
      </defs>
      <polygon points="0,0 394,0 284,470 0,470" fill="url(#panelFill)"/>
    </svg>
    <div class="front__mark" aria-hidden="true"></div>
    <div class="wordmark front__wordmark">TalkHarbor</div>
    <div class="person">
      <div class="person__name">OWEN CLARKE</div>
      <div class="person__title">CEO/FOUNDER</div>
    </div>
    <ul class="contacts">
      <li>614 208 3957
        <svg viewBox="0 0 18 18" aria-hidden="true"><rect x="5" y="1" width="9" height="16" rx="2" fill="none" stroke="#0a8fc6" stroke-width="1.6"/><rect x="7.5" y="13.5" width="4" height="1.4" fill="#0a8fc6"/></svg>
      </li>
      <li>Info@talkharbor.co.uk
        <svg viewBox="0 0 18 18" aria-hidden="true"><rect x="1" y="4" width="16" height="11" fill="#0a8fc6"/><path d="M1 4 L9 10 L17 4" fill="none" stroke="#ffffff" stroke-width="1.3"/></svg>
      </li>
      <li>www.talkharbor.co.uk
        <svg viewBox="0 0 18 18" aria-hidden="true"><circle cx="9" cy="9" r="8" fill="#0a8fc6"/><path d="M5 6 Q8 4 9 7 Q8 10 5 9 Z M10 11 Q13 10 13 13 Q11 15 10 11 Z" fill="#ffffff"/></svg>
      </li>
    </ul>
  </section>

  <section class="card card--back">
    <div class="back__ring">
      <span class="wordmark back__wordmark">TalkHarbor</span>
    </div>
    <p class="back__site">www.talkharbor.co.uk</p>
  </section>
</main>
</body>
</html>
```